The Brandwell Firm

We need a new design for our letterhead and envelopes. We are a personal injury and criminal defense firm so we need something modern and clean, but more on the professional/traditional side. Our new logo has two colors and is attached to the file so we need something that works well with those colors/matches the design. The following information needs to be on the letterhead:
Phone: (555) 214-3370
Fax: (555) 214-5186
Toll-Free: (888) 431-2059
Post Office Box 4721
Millbrook, SC 29555-4721
HarmClaimCounsel.example
PalmettoTrialAdvocates.example

Target Market(s)

Clients, government agencies, other law firms

Industry/Entity Type

Legal

Font styles to use
Sans Serif
Other font styles liked:
• Arial

Colors

Designer to choose colors to be used in the design.

Requirements
Must have
• Must look professional and clean, modern
Nice to have
• I would like to see a design that works with the logo but does not distract from the content that will be printed on it
Should not have
• Too many colors or crazy designs.

```html
<!DOCTYPE html>
<html lang="en">
<head>
<meta charset="utf-8">
<title>The Brandwell Firm — Stationery</title>
<link rel="stylesheet" href="https://fonts.googleapis.com/css2?family=Open+Sans:wght@400;600&display=swap">
<style>
  :root {
    --backdrop: #5a5a5c;
    --paper: #ffffff;
    --brand-red: #d52b2b;
    --brand-blue: #2e3192;
    --ink: #2b2b2b;
    --rule: #3a3a3a;
    --flap-shadow: rgba(0,0,0,0.18);
  }
  * { box-sizing: border-box; margin: 0; padding: 0; }
  html, body { width: 1200px; height: 904px; overflow: hidden; }
  body {
    background: var(--backdrop);
    font-family: "Open Sans", Arial, sans-serif;
    color: var(--ink);
    position: relative;
  }
  .sheet { position: absolute; background: var(--paper); }

  .letterhead { left: 81px; top: 92px; width: 502px; height: 709px; }
  .envelope-front { left: 615px; top: 234px; width: 518px; height: 259px; }
  .envelope-back { left: 615px; top: 530px; width: 518px; height: 260px; overflow: hidden; }

  .wordmark {
    display: flex; align-items: center; gap: 6px;
    color: var(--brand-blue); font-weight: 600; white-space: nowrap;
    letter-spacing: 0.02em;
  }
  .wordmark-dot {
    width: 12px; height: 12px; border-radius: 50%;
    background: var(--brand-red); flex: none;
  }
  .letterhead .wordmark {
    position: absolute; top: 152px; left: 50%; transform: translate(-50%, -100%);
    font-size: 18px; top: 172px;
  }
  .letterhead-footer {
    position: absolute; left: 34px; right: 34px; top: 664px;
    border-top: 1px solid var(--rule);
    padding-top: 8px; text-align: center;
    font-size: 7.6px; line-height: 13px;
  }
  .contact-icon { width: 7px; height: 7px; vertical-align: -1px; fill: var(--brand-blue); }

  .envelope-front .wordmark {
    position: absolute; left: 30px; top: 50px; font-size: 15px;
  }
  .return-address {
    position: absolute; left: 50px; top: 97px;
    font-size: 7.8px; line-height: 11px; text-align: center;
  }

  .flap { position: absolute; left: 0; top: 0; width: 518px; height: 100px; }
  .envelope-back .wordmark {
    position: absolute; left: 50%; top: 52px; transform: translate(-50%, -50%);
    font-size: 13px;
  }
</style>
</head>
<body>

<section class="sheet letterhead" aria-label="Letterhead">
  <div class="wordmark"><span class="wordmark-dot"></span>The Brandwell Firm</div>

  <footer class="letterhead-footer">
    <p>Post Office Box 4721, Millbrook, SC 29555-4721 |
      <svg class="contact-icon" viewBox="0 0 10 10" aria-hidden="true"><path d="M1 3 Q5 0 9 3 L8 4.5 L6.5 3.8 L6.5 3 Q5 2.5 3.5 3 L3.5 3.8 L2 4.5 Z M2.5 5 H7.5 L8.5 9 H1.5 Z"/></svg>
      (555) 214-3370 |
      <svg class="contact-icon" viewBox="0 0 10 10" aria-hidden="true"><path d="M2.5 1 H7.5 V4 H2.5 Z M1 4.5 H9 V9 H1 Z"/></svg>
      (555) 214-5186 |
      <svg class="contact-icon" viewBox="0 0 10 10" aria-hidden="true"><path d="M2 1 L4 1 L5 3.5 L3.8 4.5 Q4.8 6.2 6 6.8 L7 5.6 L9 6.8 L9 8.5 Q5 9.5 2 5.5 Q1 3 2 1 Z"/></svg>
      (888) 431-2059</p>
    <p>HarmClaimCounsel.example | PalmettoTrialAdvocates.example</p>
  </footer>
</section>

<section class="sheet envelope-front" aria-label="Envelope front">
  <div class="wordmark"><span class="wordmark-dot"></span>The Brandwell Firm</div>
  <address class="return-address" style="font-style:normal">
    Post Office Box 4721<br>Millbrook, SC 29555-4721
  </address>
</section>

<section class="sheet envelope-back" aria-label="Envelope back">
  <svg class="flap" viewBox="0 0 518 100" aria-hidden="true">
    <path d="M0 0 Q10 42 45 50 L240 86 Q259 90 278 86 L473 50 Q508 42 518 0 Z"
          fill="var(--flap-shadow)" transform="translate(0 4)"/>
    <path d="M0 0 Q10 42 45 50 L240 86 Q259 90 278 86 L473 50 Q508 42 518 0 Z"
          fill="var(--paper)"/>
  </svg>
  <div class="wordmark"><span class="wordmark-dot"></span>The Brandwell Firm</div>
</section>

</body>
</html>
```